BrivoTerna. Lantern of the Steady Harvest. Business card

Professional business card for BrivoTerna (Lantern of the Steady Harvest)
My rationale: Strategy-> Execution-> Results-> Value that lead to the BrivoTerna name: We put the Lantern of the Steady Harvest.
We deliver value to our customers helping them at defining a good strategy (cyan arrow). 90% of well formulated strategies fail due to poor execution so we also consider strategical execution very important (green arrow). Due to the execution we obtain the results (blue arrow). Finally, the results provide feedback to redefine strategy, and the new strategy has to be executed and new results obtained providing new feedback and on and on. It's like a wheel that finally, must create corporate value: value for shareholders, staholders, employees, providers...-

Target Market(s)

CEOs and steering comitees , invewrnent funds

Industry/Entity Type

Business Consultant

Contact Information for Business Card

Teodoro Vinsquel
CEO & Founder
teodoro.vinsquel@brivoterna-example.com
Mobile: +34 655.803.912
www.brivoterna-example.com

Colors

Designer to choose colors to be used in the design.

Requirements
Nice to have
• Nice to hace the words: Strategy, execution, results
• Nice to vave the claim: Lantern of the Steady Harvest
• The three colors should be shown:
• cyan for STRATEGY
• green for EXECUTION
• blue for RESULTS
Should not have
• Complete black background

```html
<!DOCTYPE html>
<html lang="en">
<head>
<meta charset="utf-8">
<title>BrivoTerna – Business Card</title>
<link href="https://fonts.googleapis.com/css2?family=Roboto:wght@300;400;700&display=swap" rel="stylesheet">
<style>
  :root {
    --backdrop: #9f9fa1;
    --royal-blue: #023399;
    --cyan: #00aeef;
    --green: #99cc33;
    --white: #ffffff;
  }
  * { margin: 0; padding: 0; box-sizing: border-box; }
  html, body {
    width: 1200px; height: 900px; overflow: hidden;
    background: var(--backdrop);
    font-family: "Roboto", Arial, sans-serif;
  }
  .canvas { position: relative; width: 1200px; height: 900px; }

  .card {
    position: absolute;
    left: 363px;
    width: 475px; height: 271px;
    overflow: hidden;
  }

  /* Front */
  .card-front { top: 145px; background: var(--royal-blue); }
  .card-front .brand-name {
    position: absolute; right: 30px; top: 196px;
    font-weight: 700; font-size: 41px; letter-spacing: -1px;
    color: var(--white); line-height: 1;
  }

  /* Back */
  .card-back { top: 484px; background: var(--white); }
  .card-back .bands { position: absolute; inset: 0; width: 475px; height: 271px; }
  .card-back .brand-name {
    position: absolute; left: 24px; top: 106px;
    font-weight: 700; font-size: 39px; letter-spacing: -1px;
    color: var(--royal-blue); line-height: 1;
  }
  .person {
    position: absolute; right: 23px; top: 24px; text-align: right;
  }
  .person-name { font-weight: 700; font-size: 16.5px; color: var(--cyan); line-height: 1.15; }
  .person-role { font-weight: 400; font-size: 11.5px; color: var(--royal-blue); line-height: 1.3; }

  .contacts {
    position: absolute; right: 22px; top: 197px;
    list-style: none; text-align: right;
  }
  .contacts li {
    display: flex; justify-content: flex-end; align-items: center;
    gap: 8px; height: 18px;
    font-weight: 300; font-size: 11.5px; color: var(--white);
  }
  .contacts svg { width: 10px; height: 10px; flex: none; }
</style>
</head>
<body>
<div class="canvas">

  <section class="card card-front">
    <div class="brand-name">BrivoTerna</div>
  </section>

  <section class="card card-back">
    <svg class="bands" viewBox="0 0 475 271" aria-hidden="true">
      <polygon fill="var(--green)" points="0,222 475,142 475,150 0,230"/>
      <polygon fill="var(--royal-blue)" points="0,240 475,160 475,271 0,271"/>
    </svg>

    <div class="brand-name">BrivoTerna</div>

    <div class="person">
      <div class="person-name">Teodoro Vinsquel</div>
      <div class="person-role">CEO &amp; Founder</div>
    </div>

    <ul class="contacts">
      <li>+34 655.803.912
        <svg viewBox="0 0 10 10"><path fill="var(--cyan)" d="M2,0.5 L3.6,2.6 L2.8,3.6 C3.4,4.9 4.9,6.4 6.3,7.1 L7.3,6.3 L9.5,7.9 L8.4,9.5 C4.5,9.3 0.7,5.5 0.5,1.6 Z"/></svg>
      </li>
      <li>www.brivoterna-example.com
        <svg viewBox="0 0 10 10"><circle cx="5" cy="5" r="4.5" fill="var(--cyan)"/><path d="M1,5 H9 M5,0.8 C3,3 3,7 5,9.2 M5,0.8 C7,3 7,7 5,9.2" stroke="var(--royal-blue)" stroke-width="0.8" fill="none"/></svg>
      </li>
      <li>teodoro.vinsquel@brivoterna-example.com
        <svg viewBox="0 0 10 10"><rect x="0.5" y="2" width="9" height="6.5" fill="var(--cyan)"/><path d="M0.8,2.3 L5,5.8 L9.2,2.3" stroke="var(--royal-blue)" stroke-width="0.8" fill="none"/></svg>
      </li>
    </ul>
  </section>

</div>
</body>
</html>
```